National Sales - Pick Up Truck Dealer

We need a logo design for a new vehicle dealership based in Sydney, Australia. The business name is Coastal Iron Haulers Motor Co. We will be selling American 'trucks/pick up trucks' like KRV, Torvan, Blaxer, Morrow T420, Kenzo Raptors, Morrow T640 and the likes.

These vehicles are a luxury option and we would like the logo to be strong, luxurious and masculine.Colours will be black and red or black and blue with the option of grey and white.

Target Market(s)

Men

Industry/Entity Type

Car Dealer

Contact Information for Business Card

Dennis Harlowe
Managing Director
0412 639 274
den@qelvtrk.com.au

Level 8, Brindle Parkway
17 Pemberly Lane
Carrow Heights
NSW
Australia
Licence No: MD493152

Back of the card

qelvtrk.com.au

Font styles to use
Sans Serif

Colors

Designer to choose colors to be used in the design.

Requirements
Must have
• The company logo that is in the attachments, you can choose from the three which one you would like to work with. Must have vehicle images ....Please look at the attachments as they show examples of what we like and also provides potential images. If you choose to put an image on the front even if it is just the front of the vehicle can you please use the Black KRV Sorrento. Must have all details from the business card details section front and back
Nice to have
• N/A
Should not have
• No cars or standard trucks, please refer to the attached images to understand the product . Should not have any new logos or branding. No other colours besides what is in the logo you choose.

```html
<!DOCTYPE html>
<html lang="en">
<head>
<meta charset="utf-8">
<title>Coastal Iron Haulers Motor Co – Business Card</title>
<link rel="stylesheet" href="https://fonts.googleapis.com/css2?family=Oswald:wght@600&family=Open+Sans:wght@400;600;700&display=swap">
<style>
  :root {
    --stage: #2a2a2b;
    --card: #262627;
    --ink-white: #f2f2f2;
    --ink-grey: #c9c9c9;
    --ink-emboss: #3a3a3b;
    --brand-blue: #1f6fc0;
    --rule: #e6e6e6;
  }
  * { box-sizing: border-box; margin: 0; padding: 0; }
  html, body { width: 1200px; height: 900px; overflow: hidden; }
  body {
    background: var(--stage);
    font-family: "Open Sans", sans-serif;
    display: flex;
    flex-direction: column;
    align-items: center;
    justify-content: center;
    gap: 40px;
  }
  .card {
    width: 660px;
    height: 377px;
    background: var(--card);
    position: relative;
    box-shadow: 0 10px 30px rgba(0,0,0,.45);
  }

  /* Back */
  .card-back .wordmark {
    position: absolute;
    top: 110px; left: 0; right: 0;
    text-align: center;
    font-weight: 700;
    font-size: 34px;
    line-height: 1.15;
    letter-spacing: 1px;
    text-transform: uppercase;
    color: var(--ink-emboss);
  }
  .card-back .web {
    position: absolute;
    bottom: 26px; left: 0; right: 0;
    text-align: center;
    font-size: 15px;
    letter-spacing: 1.5px;
    color: var(--ink-grey);
  }
  .accent { color: var(--brand-blue); }

  /* Front */
  .card-front .wordmark {
    position: absolute;
    left: 20px; top: 132px;
    width: 310px;
    text-align: center;
    font-weight: 700;
    font-size: 30px;
    line-height: 1.15;
    letter-spacing: .5px;
    text-transform: uppercase;
    color: var(--ink-white);
  }
  .divider {
    position: absolute;
    left: 345px; top: 60px;
    width: 2px; height: 250px;
    background: var(--rule);
  }
  .details {
    position: absolute;
    left: 368px; top: 56px;
    color: var(--ink-white);
  }
  .person-name {
    font-family: "Oswald", sans-serif;
    font-weight: 600;
    font-size: 36px;
    line-height: 1;
    color: var(--brand-blue);
    text-transform: uppercase;
  }
  .person-title {
    font-weight: 700;
    font-size: 16px;
    margin-top: 2px;
  }
  .licence {
    margin-top: 14px;
    font-size: 14px;
  }
  .licence .label { color: var(--brand-blue); }
  .address {
    margin-top: 8px;
    font-size: 14px;
    line-height: 1.3;
    font-style: normal;
  }
  .contact-list {
    list-style: none;
    margin-top: 12px;
    font-size: 15px;
  }
  .contact-list li {
    display: flex;
    align-items: center;
    gap: 12px;
    height: 24px;
  }
  .contact-list svg {
    width: 16px; height: 16px;
    stroke: var(--brand-blue);
    fill: none;
    stroke-width: 1.6;
    flex: none;
  }
</style>
</head>
<body>

  <section class="card card-back">
    <div class="wordmark">Coastal Iron Haulers<br>Motor Co</div>
    <div class="web">www.<span class="accent">qelvtrk</span>.com.au</div>
  </section>

  <section class="card card-front">
    <div class="wordmark">Coastal Iron<br>Haulers Motor Co</div>
    <div class="divider"></div>
    <div class="details">
      <h1 class="person-name">Dennis Harlowe</h1>
      <p class="person-title">Managing Director</p>
      <p class="licence"><span class="label">Licence No:</span> MD493152</p>
      <address class="address">
        Level 8, Brindle Parkway,<br>
        17 Pemberly Lane, Carrow Heights,<br>
        NSW, Australia
      </address>
      <ul class="contact-list">
        <li>
          <svg viewBox="0 0 16 16" aria-hidden="true"><rect x="4" y="1" width="8" height="14" rx="1.5"/><line x1="7" y1="12.5" x2="9" y2="12.5"/></svg>
          0412 639 274
        </li>
        <li>
          <svg viewBox="0 0 16 16" aria-hidden="true"><rect x="1" y="3" width="14" height="10" rx="1"/><polyline points="1,3 8,9 15,3"/></svg>
          den@qelvtrk.com.au
        </li>
        <li>
          <svg viewBox="0 0 16 16" aria-hidden="true"><circle cx="8" cy="8" r="6.5"/><ellipse cx="8" cy="8" rx="3" ry="6.5"/><line x1="1.5" y1="8" x2="14.5" y2="8"/></svg>
          <span>www.<span class="accent">qelvtrk</span>.com.au</span>
        </li>
      </ul>
    </div>
  </section>

</body>
</html>
```